Awesome photographers card for an awesome new business

Double sided business card Black background and silver logo in middle on one side. Details on otherside. please keep it simple

Industry/Entity Type

Photographer

Contact Information for Business Card

Gerald Fenwick
0452817360
GeraldFenwickPhotography47@mailbox.test
www.GeraldFenwickPhotography.test.au
Instagram _Gerald_fenwick

Requirements
Must have
• My logo in Silver
• please use instagram logo instead of "Instagram"

```html
<!DOCTYPE html>
<html lang="en">
<head>
<meta charset="utf-8">
<title>Gerald Fenwick Photography – Business Card</title>
<link rel="stylesheet" href="https://fonts.googleapis.com/css2?family=Questrial&display=swap">
<style>
  :root {
    --backdrop: #c9c9c9;
    --card-front: #f7f7f7;
    --card-back: #141414;
    --ink: #555555;
    --ink-soft: #4a4a4a;
    --rule: #6a6a6a;
    --silver: #b9b9b9;
    --silver-dark: #8a8a8a;
    --band-dark: #6f6f6f;
    --white: #ffffff;
  }
  * { box-sizing: border-box; margin: 0; padding: 0; }
  html, body {
    width: 1200px; height: 960px; overflow: hidden;
    background: var(--backdrop);
    font-family: "Questrial", "Century Gothic", sans-serif;
  }
  .canvas { position: relative; width: 1200px; height: 960px; }

  .card {
    position: absolute; width: 600px; height: 342px;
    border-radius: 16px; overflow: hidden;
  }
  .card--front { left: 322px; top: 126px; background: var(--card-front); }
  .card--back { left: 320px; top: 501px; background: var(--card-back); }

  .brand-mark {
    position: absolute; display: flex; align-items: center; justify-content: center;
    border-radius: 50%; border: 3px solid var(--silver);
    color: var(--silver); text-align: center; letter-spacing: 0.12em;
    text-transform: uppercase; line-height: 1.3;
  }
  .card--front .brand-mark {
    left: 424px; top: 38px; width: 132px; height: 132px;
    font-size: 12px; border-color: var(--silver-dark); color: var(--silver-dark);
  }
  .card--back .brand-mark {
    left: 195px; top: 66px; width: 210px; height: 210px;
    font-size: 19px; border-width: 4px;
  }

  .holder-name {
    position: absolute; left: 31px; top: 199px;
    font-size: 20px; color: var(--ink); letter-spacing: 0.02em; text-transform: uppercase;
  }
  .holder-rule {
    position: absolute; left: 31px; top: 229px; width: 528px; height: 1px;
    background: var(--rule);
  }
  .contact-list {
    position: absolute; left: 31px; top: 241px; list-style: none;
    font-size: 14px; color: var(--ink-soft);
  }
  .contact-list li { display: flex; align-items: center; height: 19px; }
  .contact-list svg { width: 13px; height: 13px; margin-right: 11px; fill: var(--ink-soft); }
  .social-square { width: 11px; height: 11px; margin: 0 12px 0 1px; background: var(--ink-soft); border-radius: 2px; }

  .footer-band { position: absolute; left: 0; bottom: 0; width: 600px; height: 30px; }
  .web-address {
    position: absolute; right: 12px; bottom: 6px;
    font-size: 14px; color: var(--white); letter-spacing: 0.01em;
  }
</style>
</head>
<body>
<main class="canvas">
  <section class="card card--front" aria-label="Business card front">
    <div class="brand-mark">Gerald<br>Fenwick</div>

    <h1 class="holder-name">Gerald Fenwick</h1>
    <div class="holder-rule"></div>

    <ul class="contact-list">
      <li>
        <svg viewBox="0 0 24 24" aria-hidden="true"><path d="M6.6 10.8a15.1 15.1 0 0 0 6.6 6.6l2.2-2.2a1 1 0 0 1 1-.25 11.4 11.4 0 0 0 3.6.57 1 1 0 0 1 1 1V20a1 1 0 0 1-1 1A17 17 0 0 1 3 4a1 1 0 0 1 1-1h3.5a1 1 0 0 1 1 1c0 1.25.2 2.45.57 3.57a1 1 0 0 1-.25 1z"/></svg>
        0452817360
      </li>
      <li>
        <svg viewBox="0 0 24 24" aria-hidden="true"><path d="M2 5h20v14H2z M2 5l10 8 10-8" fill="none" stroke="#4a4a4a" stroke-width="0"/><path d="M2 5h20v2l-10 7L2 7z"/><path d="M2 9l10 7 10-7v10H2z"/></svg>
        GeraldFenwickPhotography47@mailbox.test
      </li>
      <li>
        <span class="social-square" aria-hidden="true"></span>
        Gerald_fenwick
      </li>
    </ul>

    <svg class="footer-band" viewBox="0 0 600 30" aria-hidden="true">
      <defs>
        <linearGradient id="bandSilver" x1="0" x2="1" y1="0" y2="0">
          <stop offset="0" stop-color="#9a9a9a"/>
          <stop offset="1" stop-color="#d8d8d8"/>
        </linearGradient>
        <linearGradient id="bandDark" x1="0" x2="1" y1="0" y2="0">
          <stop offset="0" stop-color="#8a8a8a"/>
          <stop offset="1" stop-color="#5e5e5e"/>
        </linearGradient>
      </defs>
      <rect x="0" y="12" width="300" height="18" fill="url(#bandSilver)"/>
      <polygon points="296,30 318,2 600,2 600,30" fill="url(#bandDark)"/>
    </svg>
    <p class="web-address">www.GeraldFenwickPhotography.test.au</p>
  </section>

  <section class="card card--back" aria-label="Business card back">
    <div class="brand-mark">Gerald<br>Fenwick</div>
  </section>
</main>
</body>
</html>
```